Website Design for a Project Management Consulting Business

I have a logo design already and now I need a website.
I am a project manager and run my own consulting business.
Currently I am under contract with 3 major Vantage 400 companies. I'd like a website I can direct current and future clients.
My job is running IT projects and working with developers to deliver business priorities.
The website should be professional and clean - I work IT projects and would like to incorporate that into any theme.
I'd like the site to have several page or breakoff links - sections would include : about me, about my services, a page to display all of my certification badges, another page to talk about highlights from past projects and so on.
Looking for a collaborative experience.

Industry/Entity Type

Vantage 400 Consulting Firm - Project Management

Coding

Coded - Design and coding required

Number of Pages Required

1 page

Font styles to use
Serif

Colors
0094D4
00A9DD
6FCCEA
C7EBF8
E9F6FB
EE7325
F08F49
F5BC92
FAE3D3
FDF4ED

Requirements
Must have
• Sections that are a must: About Me (bio), About My Services, About my Certifications and Credentials, Experience on Past Projects,
Nice to have
• I have added the logo below - I'd like to use the logo and have it prominent ; should be professional and inviting

```html
<!DOCTYPE html>
<html lang="en">
<head>
<meta charset="utf-8">
<title>Meridian — Project Management Consulting</title>
<link href="https://fonts.googleapis.com/css2?family=Red+Hat+Display:wght@400;500;600;700;800&display=swap" rel="stylesheet">
<style>
:root{
  --navy:#0b3a6e;
  --navy-deep:#0a3564;
  --sky:#1ea0da;
  --cta:#1ba3dd;
  --orange:#ee7325;
  --orange-soft:#f08f49;
  --ink:#111111;
  --body:#3a3a3a;
  --muted:#9a9a9a;
  --paper:#ffffff;
  --mist:#eef0f3;
  --black:#050505;
}
*{margin:0;padding:0;box-sizing:border-box}
html,body{width:1200px;height:5394px;overflow:hidden}
body{font-family:"Red Hat Display",Arial,sans-serif;color:var(--ink);background:var(--paper);position:relative}
section,header,footer{position:absolute;left:0;width:1200px}
.abs{position:absolute}
.btn{position:absolute;display:flex;align-items:center;justify-content:center;font-size:13px;font-weight:700;color:var(--ink);background:var(--paper);border:2px solid var(--orange)}
.media{position:absolute}

/* header + hero */
.hero{top:0;height:676px;background:
  radial-gradient(circle at 1120px 170px,rgba(150,90,200,.45),transparent 260px),
  radial-gradient(circle at 1000px 60px,rgba(240,140,180,.35),transparent 220px),
  radial-gradient(circle at 1180px 620px,rgba(90,110,220,.3),transparent 230px),
  radial-gradient(circle at 40px 540px,rgba(120,140,230,.15),transparent 200px),
  var(--paper)}
.brand{left:175px;top:22px;display:flex;align-items:center;gap:10px}
.brand-mark{width:34px;height:34px;border:3px solid var(--navy)}
.brand-name{font-size:26px;font-weight:700;color:var(--navy);letter-spacing:.5px}
.nav{left:524px;top:26px;display:flex;gap:24px;font-size:13px;font-weight:600}
.nav-contact{left:903px;top:18px;width:120px;height:38px}
.hero-title{left:175px;top:150px;font-size:74px;line-height:82px;font-weight:800;color:var(--sky);letter-spacing:-.5px}
.hero-sub{left:175px;top:336px;font-size:32px;font-weight:700}
.hero-btn{left:175px;top:412px;width:135px;height:36px}
.partners{left:175px;top:545px;width:855px;display:flex;justify-content:space-between;align-items:center;color:var(--muted);font-size:19px;font-weight:600}

/* about */
.about{top:676px;height:751px;background:radial-gradient(circle at 1150px 650px,rgba(120,120,220,.45),transparent 260px),var(--navy)}
.about-name{left:180px;top:108px;font-size:42px;font-weight:600;color:#fff}
.about-role{left:180px;top:166px;font-size:20px;color:#dbe6f2}
.about-bio{left:180px;top:236px;width:390px;font-size:20px;line-height:31px;color:#fff}
.signature{left:175px;top:472px;width:210px;height:60px;background:linear-gradient(90deg,rgba(255,255,255,.25),rgba(255,255,255,.08));border-radius:30px}
.portrait-frame{left:592px;top:154px;width:395px;height:485px;border:1px solid rgba(255,255,255,.2)}
.portrait{left:611px;top:112px;width:414px;height:508px;background:linear-gradient(160deg,#4b4b4b,#1a1a1a 70%)}

/* services */
.services{top:1427px;height:940px;background:linear-gradient(180deg,#e4e6ea,var(--mist) 40%,#f4f5f7)}
.services h2{position:absolute;left:175px;top:156px;font-size:42px;font-weight:700;color:var(--navy)}
.services-lead{left:175px;top:222px;width:340px;font-size:13px;line-height:21px;color:var(--body)}
.svc-card{position:absolute;color:#fff;font-size:21px;font-weight:600}
.svc-card span{position:absolute;left:36px}
.svc-1{left:175px;top:321px;width:413px;height:337px;background:linear-gradient(150deg,#5a4a3c,#2c2a2a 60%,#6a5a4a)}
.svc-2{left:611px;top:114px;width:414px;height:336px;background:linear-gradient(150deg,#6a5c54,#2a2f3a 60%,#1c1f27)}
.svc-3{left:611px;top:473px;width:414px;height:336px;background:linear-gradient(150deg,#4f5a4a,#2e3236 60%,#3a3d42)}
.svc-detail{left:630px;top:656px;width:377px;height:175px;background:#fff;padding:28px 30px;box-shadow:0 10px 30px rgba(0,0,0,.08)}
.svc-detail h3{font-size:22px;font-weight:600;color:var(--navy);margin-bottom:14px}
.svc-detail p{font-size:13px;line-height:22px;color:var(--body)}
.svc-btn{left:175px;top:700px;width:145px;height:43px;background:var(--orange);border:none;color:#fff}

/* certifications */
.certs{top:2367px;height:801px;background:radial-gradient(circle at 0 780px,rgba(120,110,220,.3),transparent 200px),radial-gradient(circle at 1200px 740px,rgba(120,110,220,.25),transparent 200px),var(--paper)}
.certs h2{position:absolute;left:175px;top:100px;font-size:42px;font-weight:700;color:var(--navy)}
.cert{position:absolute;top:184px;width:270px}
.cert-img{height:271px}
.cert h3{margin-top:24px;font-size:21px;font-weight:600}
.cert p{margin-top:12px;font-size:13px;line-height:22px;color:var(--body)}
.cert-1{left:175px}.cert-1 .cert-img{background:linear-gradient(150deg,#3a4038,#70706a 60%,#a8a29a)}
.cert-2{left:466px}.cert-2 .cert-img{background:linear-gradient(150deg,#d8d8d6,#bdbdbb 60%,#e8e8e6)}
.cert-3{left:757px}.cert-3 .cert-img{background:linear-gradient(150deg,#e8a070,#c8d4e8 55%,#7ea0d0)}
.cert-btn{left:535px;top:651px;width:130px;height:40px;border:2px solid var(--ink)}

/* projects */
.projects{top:3168px;height:862px;background:radial-gradient(circle at 60px 330px,rgba(120,80,160,.55),transparent 300px),radial-gradient(circle at 1150px 150px,rgba(40,50,140,.4),transparent 260px),var(--black);color:#fff}
.projects h2{position:absolute;left:247px;top:116px;font-size:42px;font-weight:600}
.project-img{left:247px;top:192px;width:705px;height:335px;background:linear-gradient(150deg,#6f8068,#a8b4a8 45%,#3c4a58 70%,#c8cac4)}
.project-title{left:247px;top:555px;font-size:22px;font-weight:600}
.project-text{left:247px;top:600px;width:705px;font-size:13px;line-height:22px;color:#e6e6e6}
.arrows{left:245px;top:728px}

/* why */
.why{top:4030px;height:625px;background:radial-gradient(circle at 1150px 500px,rgba(150,140,230,.3),transparent 230px),var(--paper)}
.why h2{position:absolute;left:175px;top:104px;font-size:42px;font-weight:700;color:var(--navy)}
.why-list{left:177px;top:198px;list-style:none;font-size:21px;font-weight:600}
.why-list li{height:65px}
.why-list .active{text-decoration:underline;color:var(--navy)}
.why-rule{left:600px;top:190px;width:1px;height:340px;background:#e4e4e4}
.why-mark{left:599px;top:335px;width:3px;height:40px;background:var(--orange)}
.why-icon{left:638px;top:190px}
.why-text{left:640px;top:300px;width:390px;font-size:17px;line-height:27px;color:var(--body)}

/* cta */
.cta{top:4655px;height:335px;background:var(--cta);color:#fff;text-align:center}
.cta h2{position:absolute;left:0;top:86px;width:1200px;font-size:42px;line-height:48px;font-weight:600}
.cta-btn{left:540px;top:225px;width:120px;height:44px;border:none}

/* footer */
.footer{top:4990px;height:404px;background:var(--navy-deep);color:#fff}
.foot-brand{left:175px;top:102px;width:190px;height:58px;background:#fff;display:flex;align-items:center;justify-content:center;gap:8px}
.foot-brand .brand-mark{width:24px;height:24px;border-width:2px}
.foot-brand .brand-name{font-size:19px}
.social{left:180px;top:218px;display:flex;gap:24px}
.social span{width:14px;height:14px;border-radius:50%;background:#fff;display:block}
.foot-links{left:488px;top:92px;list-style:none;font-size:16px;font-weight:600;line-height:42px}
.offices{left:765px;top:92px;width:270px;font-size:16px;line-height:26px}
.offices h4{font-size:16px;font-weight:600;margin-bottom:14px}
.offices .call{margin-top:18px}
.foot-bottom{left:175px;top:350px;width:850px;display:flex;justify-content:space-between;font-size:12px}
</style>
</head>
<body>

<header class="hero">
  <div class="abs brand"><span class="brand-mark"></span><span class="brand-name">MERIDIAN</span></div>
  <nav class="abs nav"><span>About Me</span><span>My Services</span><span>Certification</span><span>Projects</span></nav>
  <span class="btn nav-contact">Contact Us</span>
  <h1 class="abs hero-title">Lorem ipsum dolor<br>sit amet, sectetur</h1>
  <p class="abs hero-sub">Lorem ipsum dolor sit amet</p>
  <span class="btn hero-btn">Lets Connect</span>
  <div class="abs partners"><span>Larkfield</span><span>Quillpath</span><span>NORVE</span><span>Ovandel</span><span>HALDENWORKS</span></div>
</header>

<section class="about">
  <h2 class="abs about-name">John Doe</h2>
  <p class="abs about-role">UI/UX Designer and Visualizer</p>
  <p class="abs about-bio">Lorem ipsum dolor sit amet, consectetur adipiscing elit. Massa donec vitae purus aliquam facilisis aenean enim urna gravida. Non velit neque faucibus placerat orci libero massa eu tincidunt.</p>
  <div class="abs signature" role="img" aria-label="Handwritten signature"></div>
  <div class="abs portrait-frame"></div>
  <div class="media portrait" role="img" aria-label="Black and white portrait of the consultant holding a phone"></div>
</section>

<section class="services">
  <h2>Our Services</h2>
  <p class="abs services-lead">As a full-stack app development agency, we provide full-service app design and development teams for Phone, Tablet, Desktop, and Web apps.</p>
  <div class="svc-card svc-2" role="img" aria-label="Hands on a laptop showing code"><span style="top:240px">Services Detail 02</span></div>
  <div class="svc-card svc-1" role="img" aria-label="Person holding a phone in front of a laptop"><span style="top:275px">Services Detail 01</span></div>
  <div class="svc-card svc-3" role="img" aria-label="Desk with a plant and a phone"></div>
  <div class="abs svc-detail"><h3>Services Detail 03</h3><p>Lorem ipsum dolor sit amet, consectetur adipiscing elit. Lorem ipsum dolor sit amet, consectetur adipiscing elit.</p></div>
  <span class="btn svc-btn">Lets take a call</span>
</section>

<section class="certs">
  <h2>Certifications and Credentials</h2>
  <div class="cert cert-1"><div class="cert-img" role="img" aria-label="Developer working at monitors"></div><h3>Certificate detail</h3><p>Lorem ipsum dolor sit amet, consectetur adipiscing elit. Lorem ipsum dolor sit amet, consectetur adipiscing elit.</p></div>
  <div class="cert cert-2"><div class="cert-img" role="img" aria-label="Certificate paper with a tablet"></div><h3>Certificate detail</h3><p>Lorem ipsum dolor sit amet, consectetur adipiscing elit. Lorem ipsum dolor sit amet, consectetur adipiscing elit.</p></div>
  <div class="cert cert-3"><div class="cert-img" role="img" aria-label="Laptop with a city skyline at sunset"></div><h3>Certificate detail</h3><p>Lorem ipsum dolor sit amet, consectetur adipiscing elit. Lorem ipsum dolor sit amet, consectetur adipiscing elit.</p></div>
  <span class="btn cert-btn">Start with us</span>
</section>

<section class="projects">
  <h2>Experience on Past Projects</h2>
  <div class="media project-img" role="img" aria-label="Laptop with a dashboard beside a cup of coffee"></div>
  <h3 class="abs project-title">Lorem ipsum dolor sit amet, consectetur adipiscing elit</h3>
  <p class="abs project-text">Lorem ipsum dolor sit amet, consectetur adipiscing elit. Massa donec vitae purus aliquam facilisis aenean enim urna gravida. Non velit neque faucibus placerat orci libero massa eu tincidunt. Lorem ipsum dolor sit amet, consectetur adipiscing elit. Massa donec vitae purus aliquam facilisis aenean enim urna gravida. Non velit neque faucibus placerat orci libero massa eu tincidunt.</p>
  <svg class="abs arrows" width="100" height="20" viewBox="0 0 100 20" aria-label="Previous and next">
    <path d="M32 10H2M10 3L2 10l8 7" fill="none" stroke="#fff" stroke-width="2.5"/>
    <path d="M60 10h30M82 3l8 7-8 7" fill="none" stroke="#ee7325" stroke-width="2.5"/>
  </svg>
</section>

<section class="why">
  <h2>Why work with me</h2>
  <ul class="abs why-list">
    <li>Lorem ipsum dolor</li>
    <li>Lorem ipsum dolor site, dummy</li>
    <li class="active">Etiam dignissim mi eget</li>
    <li>Cras non leo sed felis pretium</li>
    <li>Ut cursus viverra faucibus</li>
  </ul>
  <div class="abs why-rule"></div>
  <div class="abs why-mark"></div>
  <svg class="abs why-icon" width="70" height="90" viewBox="0 0 70 90" aria-label="Touch icon">
    <g fill="none" stroke="#ee7325" stroke-width="3">
      <circle cx="30" cy="30" r="26"/><circle cx="30" cy="30" r="16"/><circle cx="30" cy="30" r="6"/>
      <path d="M30 36v40M30 56h14a8 8 0 0 1 8 8v20"/>
    </g>
  </svg>
  <p class="abs why-text">Lorem ipsum dolor sit amet, consectetur adipiscing elit. Etiam dignissim mi eget turpis ullamcorper ullamcorper. Donec nec posuere erat. Maecenas tristique nisi ut erat iaculis, vitae aliquet mauris mollis.</p>
</section>

<section class="cta">
  <h2>Let us help you overcome<br>your challenges</h2>
  <span class="btn cta-btn">Contact Us</span>
</section>

<footer class="footer">
  <div class="abs foot-brand"><span class="brand-mark"></span><span class="brand-name">MERIDIAN</span></div>
  <div class="abs social" aria-label="Social links"><span></span><span></span><span></span><span></span></div>
  <ul class="abs foot-links"><li>Services type 01</li><li>Services type 01</li><li>Services type 01</li><li>Services type 01</li></ul>
  <div class="abs offices"><h4>Offices</h4><p>Address line 01, Address line 02, City, Country</p><p class="call">Call : 1 123 456 7890</p></div>
  <div class="abs foot-bottom"><span>© 2022 All right reserved to meridianpm.example</span><span>Privacy Policy | Terms | Sitemap | Company Details</span></div>
</footer>

</body>
</html>
```